Flyer for Texas Schools Training and Certification Program

We need a 8.5 X 5.5 two sided flyer. One side will focus on the exclusive Certification we offer Independent Campus Accredited Fiscal Steward (ICAFS) These certified officers are prepared to run a multi-million dollar charter school. The other side will focus on the training available to all Texas Charter Board Members, Superintendents and Business Office staff. We provide required training hours that meet the QVD compliance requirements as well as CPA and GOVIK continuing education credits (CEU). Training are in the areas of Leadership, Human Resources, Finance, Grant Management and Facility Operations. Colors should be in keeping with the website. www.ICAFSGUILD.org. The flyer should include both the ICAFS and NDFR logos.

Target Market(s)

Charter School Administrators, Board Members and Business Office staff

Industry/Entity Type

Training

Requirements
Must have
• Eye catching quick read, color scheme in line with our website www.icafsguild.org.
• Clear offerings of live webinars and on-line (available 24x7) trainings
• Clear offerings meet the State required training hours - ICAFS is a State approved provider). It must have a much more professional design then the pieces I have been using.
Nice to have
• Fun, picture, feel of life is easier less hectic with ICAFS.

```html
<!DOCTYPE html>
<html lang="en">
<head>
<meta charset="utf-8">
<title>ICAFS Training Flyer</title>
<link href="https://fonts.googleapis.com/css2?family=Open+Sans:ital,wght@0,400;0,600;0,700;1,600&display=swap" rel="stylesheet">
<style>
  :root {
    --brand-red: #8e1b1e;
    --brand-red-light: #b3282c;
    --ink: #2b2b2b;
    --muted: #5e5e5e;
    --paper: #ffffff;
    --band-grey: #d9d9d9;
  }
  * { box-sizing: border-box; margin: 0; padding: 0; }
  html, body { width: 779px; height: 1200px; overflow: hidden; background: var(--paper); }
  body { font-family: "Open Sans", Arial, sans-serif; color: var(--ink); position: relative; }

  .hero-photo {
    position: absolute; left: 0; top: 0; width: 779px; height: 420px;
    background: linear-gradient(120deg, #eef0f2 0%, #cfd3d8 30%, #8b8f96 55%, #2e3a4c 75%, #dfe2e6 100%);
  }

  .sidebar { position: absolute; left: 26px; top: 450px; width: 240px; }
  .brand { display: flex; align-items: center; gap: 8px; }
  .brand-mark { width: 12px; height: 12px; background: var(--brand-red); }
  .brand-name { font-size: 28px; font-weight: 700; color: var(--brand-red); letter-spacing: 1px; line-height: 1.1; }
  .brand-full { font-size: 8.5px; color: var(--muted); margin-top: 3px; }
  .endorsed { margin-top: 36px; font-size: 11px; font-weight: 600; color: var(--ink); }
  .partner { margin-top: 8px; display: flex; align-items: center; gap: 8px; }
  .partner-mark { width: 22px; height: 22px; border-radius: 50%; background: var(--brand-red); }
  .partner-name { font-size: 22px; font-weight: 700; color: var(--brand-red); line-height: 1.1; }
  .partner-full { font-size: 8.5px; color: var(--muted); margin-top: 4px; }

  .tagline { position: absolute; top: 828px; left: 26px; width: 220px; font-size: 17px; line-height: 1.35; font-style: italic; font-weight: 600; color: var(--brand-red-light); }
  .learn-more { position: absolute; top: 912px; left: 26px; width: 230px; font-size: 12px; line-height: 1.45; color: var(--muted); }
  .learn-more strong { display: block; color: var(--ink); font-weight: 700; }

  .content { position: absolute; left: 282px; top: 432px; width: 497px; }
  .section-bar {
    background: linear-gradient(90deg, var(--brand-red) 0%, var(--brand-red-light) 100%);
    color: #fff; font-weight: 700; font-size: 14.5px; padding: 8px 16px; line-height: 1.3;
  }
  .section-body { padding: 12px 18px 18px 16px; font-size: 12px; line-height: 1.5; color: var(--muted); }
  .section-body p + p { margin-top: 12px; }
  .bullets { list-style: none; }
  .bullets li::before { content: "• "; color: var(--ink); }

  .footer-rule { position: absolute; left: 0; top: 1118px; width: 779px; height: 3px; background: var(--brand-red); }
  .footer-band { position: absolute; left: 0; top: 1121px; width: 779px; height: 79px; background: linear-gradient(180deg, #ffffff 0%, var(--band-grey) 100%); }
  .footer-url { position: absolute; left: 26px; top: 1140px; font-size: 13px; font-weight: 700; letter-spacing: 2px; color: var(--brand-red); }
</style>
</head>
<body>
  <div class="hero-photo" role="img" aria-label="Photo of smiling business professionals shaking hands in an office meeting"></div>

  <aside class="sidebar">
    <div class="brand">
      <span class="brand-mark"></span>
      <span class="brand-name">ICAFS</span>
    </div>
    <p class="brand-full">Independent Campus Accredited Fiscal Steward</p>

    <p class="endorsed">Endorsed by:</p>
    <div class="partner">
      <span class="partner-mark"></span>
      <span class="partner-name">NDFR</span>
    </div>
    <p class="partner-full">Nondistrict Family Roundtable</p>
  </aside>

  <p class="tagline">Fun, picture, feel of life is easier less hectic with ICAFS</p>
  <p class="learn-more"><strong>Learn More</strong>Visit our website and become a registered user. View our calendar and sign up for upcoming trainings.</p>

  <main class="content">
    <section>
      <h2 class="section-bar">Our Commitment</h2>
      <div class="section-body">
        <p>ICAFS® is committed to raising the competencies of charter business offices across the state of Texas. These increased business competencies help ensure your charter school is viable, stable, and fiscally sound and has a foundation of continuous improvement and growth. We are committed to keeping pace with the diverse, complex and ever changing responsibilities of a charter business officer.</p>
        <p>ACTION – Register at www.ICAFSGUILD.org and start receiving your weekly tip, and browse the variety of courses for yourself, your superintendent, board members or business office staff. All trainings are open to anyone; those pursuing certification or just expanding his or her professional development. www.ICAFSGUILD.org</p>
      </div>
    </section>

    <section>
      <h2 class="section-bar">TRAININGS – Open to Everyone</h2>
      <div class="section-body">
        <ul class="bullets">
          <li>Live Monthly Webinars</li>
          <li>On-Line 24 X 7 Courses</li>
          <li>Live Trainings throughout Texas</li>
          <li>Boot Camp – Hands on Scenario Based – Putting Knowledge to Work</li>
          <li>Business Week – Updates From the Experts</li>
          <li>Documentation Workshop – Creating Procedure Manuals and Systems</li>
          <li>All courses earn QVD Commissioner Hours, CPA CPE, and ICAFS Hours</li>
        </ul>
      </div>
    </section>

    <section>
      <h2 class="section-bar">CONQUER COMPETENCIES- Realize Continuous<br>Improvement</h2>
      <div class="section-body">
        <ul class="bullets">
          <li>Courses Offered in All Areas</li>
          <li>Courses Offered for All Levels</li>
          <li>Just in Time Training – Timed with Compliance and Time of Year</li>
          <li>Tuesday TIP – Timely How to on Current Compliance Deadlines</li>
          <li>Resource Center – Charter Business Office Specific</li>
        </ul>
      </div>
    </section>
  </main>

  <div class="footer-rule"></div>
  <div class="footer-band"></div>
  <p class="footer-url">www.icafsguild.org</p>
</body>
</html>
```